Private lender of mortgages and rent to own housing

need a website that reflects real estate especially mortgage lending and rent to own houses..
Sections as follows
Home About Types of mortgages Rent to own Contact us
Target Market(s)
consumers who require non traditonal mortgages
Industry/Entity Type
Mortgage
Coding
Coded - Design and coding required
Number of Pages Required
4 page
Font styles to use
Sans Serif
Colors
Designer to choose colors to be used in the design.
Requirements
Must have
- background pictures on pages. with nice picture on homepage of houses or a community
Nice to have
- contact us form i supplied a ink to

```html
<!DOCTYPE html>
<html lang="en">
<head>
<meta charset="utf-8">
<title>Harborline Lending Group – Rent to Own a Home</title>
<link href="https://fonts.googleapis.com/css2?family=Open+Sans:wght@400;600;700&family=Roboto:wght@400;500&display=swap" rel="stylesheet">
<style>
:root{
  --navy:#23215e;
  --royal:#2f3fd0;
  --sky-top:#3b44d6;
  --sky-mid:#4a63d8;
  --ink:#222233;
  --body:#4a4a55;
  --muted:#6a6a75;
  --footer:#ececee;
  --rule:#d6d6dc;
  --white:#ffffff;
}
*{margin:0;padding:0;box-sizing:border-box}
html,body{width:1200px;height:2456px;overflow:hidden;background:var(--white)}
body{font-family:"Roboto",Arial,sans-serif;color:var(--body);position:relative}
.page{position:relative;width:1200px;height:2456px}
a{color:inherit;text-decoration:none}

/* Hero */
.hero{position:absolute;left:0;top:0;width:1200px;height:714px;
  background:linear-gradient(180deg,var(--sky-top) 0%,var(--sky-mid) 40%,#5a5e6e 60%,#3c352f 80%,#2d2a26 100%)}
.brand{position:absolute;left:131px;top:24px;display:flex;align-items:center;gap:10px;
  font-family:"Open Sans",Arial,sans-serif;font-weight:700;font-size:15px;color:var(--white);letter-spacing:.2px;text-transform:uppercase}
.brand .mark{width:12px;height:12px;border-radius:50%;background:var(--white)}
.call{position:absolute;right:131px;top:14px;display:flex;align-items:center;gap:8px;color:var(--white)}
.call small{font-family:"Open Sans",sans-serif;font-size:10px;letter-spacing:.5px}
.call strong{font-family:"Open Sans",sans-serif;font-size:18px;font-weight:600}
.nav{position:absolute;right:131px;top:57px;display:flex;gap:38px;
  font-family:"Open Sans",sans-serif;font-weight:700;font-size:11px;color:var(--white);text-transform:uppercase}
.hero-title{position:absolute;left:0;width:1200px;top:130px;text-align:center;color:var(--white);
  font-family:"Open Sans",sans-serif;font-size:25px;font-weight:400}
.hero-sub{position:absolute;left:0;width:1200px;top:170px;text-align:center;color:#dfe3ff;
  font-family:"Open Sans",sans-serif;font-size:17px}
.dots{position:absolute;top:649px;left:560px;display:flex;gap:11px}
.dots span{width:11px;height:11px;border-radius:50%;background:var(--white)}
.dots span.off{background:transparent;border:2px solid var(--white)}

/* Section heads */
.sec-title{position:absolute;left:0;width:1200px;text-align:center;color:var(--navy);
  font-family:"Open Sans",sans-serif;font-weight:700;font-size:21px}
.sec-rule{position:absolute;left:576px;width:48px;height:2px;background:var(--navy)}

/* Services */
.service{position:absolute;width:220px;height:250px;text-align:center}
.service svg{display:block;margin:0 auto}
.service h3{position:absolute;left:0;width:220px;top:94px;font-family:"Open Sans",sans-serif;font-weight:700;font-size:12.5px;color:#111;text-transform:uppercase}
.service p{position:absolute;left:33px;width:154px;top:128px;font-size:11.5px;line-height:17.5px;color:var(--body)}
.service .more{position:absolute;left:0;width:220px;top:230px;font-family:"Open Sans",sans-serif;font-weight:700;font-size:10px;color:var(--navy)}
.service .more::after{content:"";display:block;width:20px;height:2px;background:var(--navy);margin:8px auto 0}

/* Welcome */
.welcome-bg{position:absolute;left:0;top:1174px;width:1200px;height:479px;
  background:linear-gradient(180deg,#6f9be0 0%,#b9cff0 35%,#e7eef8 60%,#d9b99b 78%,#c48160 100%)}
.welcome-panel{position:absolute;left:339px;top:1174px;width:524px;height:332px;background:rgba(255,255,255,.72)}
.welcome-panel h2{position:absolute;top:33px;left:0;width:524px;text-align:center;color:var(--navy);
  font-family:"Open Sans",sans-serif;font-weight:700;font-size:20px}
.welcome-panel p{position:absolute;top:82px;left:62px;width:400px;text-align:center;font-size:12.5px;line-height:19px;color:#333}
.btn{position:absolute;left:218px;top:231px;width:88px;height:25px;background:var(--navy);color:var(--white);
  font-family:"Open Sans",sans-serif;font-weight:700;font-size:10px;display:flex;align-items:center;justify-content:center}

.types{position:absolute;left:0;top:1653px;width:1200px;height:118px;background:var(--navy)}
.type{position:absolute;top:37px;color:var(--white);font-family:"Open Sans",sans-serif;font-size:15px;line-height:20px}
.divider{position:absolute;top:28px;width:1px;height:60px;background:rgba(255,255,255,.35)}

/* Testimonials */
.quote{position:absolute;left:388px;top:1910px;width:435px;text-align:center;font-size:12.5px;line-height:19.5px;color:#333}
.qmark{position:absolute;font-family:Georgia,serif;font-size:48px;color:#c8c8cc;line-height:1}
.author{position:absolute;left:0;width:1200px;top:2034px;text-align:center;font-family:"Open Sans",sans-serif;font-weight:700;font-size:10px;color:var(--navy)}
.arrow{position:absolute;top:1928px;width:40px;height:40px;border-radius:50%;border:1px solid #c8c8cc;display:flex;align-items:center;justify-content:center}

/* Footer */
.footer{position:absolute;left:0;top:2105px;width:1200px;height:351px;background:var(--footer)}
.f-brand{position:absolute;left:139px;top:122px;display:flex;align-items:center;gap:9px;
  font-family:"Open Sans",sans-serif;font-weight:700;font-size:14px;color:var(--navy);text-transform:uppercase}
.f-brand .mark{width:11px;height:11px;border-radius:50%;background:var(--navy)}
.f-head{position:absolute;top:63px;font-family:"Open Sans",sans-serif;font-weight:700;font-size:11px;color:var(--navy);text-transform:uppercase}
.f-contact{position:absolute;left:406px;top:98px;font-size:11.5px;color:#444}
.f-contact li{list-style:none;display:flex;gap:18px;align-items:flex-start;margin-bottom:18px;line-height:18px}
.f-contact svg{flex:none;margin-top:3px}
.f-menu{position:absolute;left:679px;top:98px;list-style:none;font-size:11px;line-height:17.5px;color:#444}
.f-input{position:absolute;left:859px;top:98px;width:210px;height:42px;background:var(--white);border:1px solid #d0d0d6;
  display:flex;align-items:center;gap:14px;padding-left:14px;font-size:11.5px;color:#555}
.f-btn{position:absolute;left:859px;top:151px;width:102px;height:37px;background:var(--navy);color:var(--white);
  font-family:"Open Sans",sans-serif;font-weight:700;font-size:12px;display:flex;align-items:center;justify-content:center}
.f-rule{position:absolute;left:131px;top:257px;width:936px;height:1px;background:var(--rule)}
.follow{position:absolute;left:131px;top:296px;display:flex;align-items:center;gap:12px;font-size:11px;color:#444}
.follow span.c{width:25px;height:25px;border-radius:50%;background:var(--royal)}
.follow .lbl{margin-right:12px}
.copy{position:absolute;right:131px;top:303px;font-size:11px;color:#444}
</style>
</head>
<body>
<div class="page">

  <header class="hero" role="img" aria-label="Photo of a large stone and shingle family home with lit garages at dusk under a blue sky">
  </header>
  <div class="brand"><span class="mark"></span>Harborline Lending Group</div>
  <div class="call">
    <svg width="12" height="12" viewBox="0 0 24 24"><path fill="#fff" d="M6.6 10.8a15.1 15.1 0 0 0 6.6 6.6l2.2-2.2c.3-.3.7-.4 1-.2 1.1.4 2.3.6 3.6.6.6 0 1 .4 1 1V20c0 .6-.4 1-1 1A17 17 0 0 1 3 4c0-.6.4-1 1-1h3.5c.6 0 1 .4 1 1 0 1.3.2 2.5.6 3.6.1.3 0 .7-.2 1z"/></svg>
    <small>CALL US :</small><strong>555.010.2040</strong>
  </div>
  <nav class="nav"><a>Home</a><a>About</a><a>Types of Mortgages</a><a>Rent to Own</a><a>Contact Us</a></nav>
  <h1 class="hero-title">Rent to Own a Home</h1>
  <p class="hero-sub">We Can Put You in Your Own Home Today</p>
  <div class="dots"><span class="off"></span><span></span><span class="off"></span><span></span><span></span></div>

  <section class="services">
    <h2 class="sec-title" style="top:760px">OUR SERVICES</h2>
    <div class="sec-rule" style="top:803px"></div>

    <div class="service" style="left:108px;top:866px">
      <svg width="60" height="60" viewBox="0 0 60 60" fill="none" stroke="#23215e" stroke-width="3"><path d="M12 24a19 19 0 0 1 34-8"/><path d="M48 36a19 19 0 0 1-34 8"/><path d="M46 8v9h-9M14 52v-9h9"/><text x="30" y="38" text-anchor="middle" font-family="Open Sans,sans-serif" font-weight="700" font-size="22" fill="#23215e" stroke="none">$</text></svg>
      <h3>Down Payment</h3>
      <p>We require a minimum down payment of $10,000 or 3.5% to 4% of total price of the home (whichever is larger).</p>
      <a class="more">READ MORE</a>
    </div>
    <div class="service" style="left:371px;top:866px">
      <svg width="60" height="60" viewBox="0 0 60 60"><circle cx="30" cy="16" r="10" fill="#23215e"/><text x="30" y="21" text-anchor="middle" font-family="Open Sans,sans-serif" font-weight="700" font-size="14" fill="#fff">$</text><path fill="#23215e" d="M8 28h5v16l9 8h5V40l-7-8 2-2 8 9v15H19L8 46zM52 28h-5v16l-9 8h-5V40l7-8-2-2-8 9v15h11l11-10z"/></svg>
      <h3>Household Income</h3>
      <p>Steady, provable household income that can support the price of the home you would like.</p>
      <a class="more">READ MORE</a>
    </div>
    <div class="service" style="left:630px;top:866px">
      <svg width="60" height="60" viewBox="0 0 60 60"><rect x="8" y="22" width="40" height="26" rx="3" fill="#23215e"/><rect x="8" y="27" width="40" height="5" fill="#fff"/><rect x="13" y="38" width="14" height="4" fill="#fff"/><path fill="#23215e" stroke="#fff" stroke-width="2" d="M30 20l16-10 8 4-4 10-18 6z"/></svg>
      <h3>Credit Report</h3>
      <p>Steady, provable household income that can support the price of the home you would like.</p>
      <a class="more">READ MORE</a>
    </div>
    <div class="service" style="left:884px;top:866px">
      <svg width="60" height="60" viewBox="0 0 60 60"><path fill="#23215e" d="M12 10h28l8 6H16zM10 40h30l-6 10H14z"/><path fill="none" stroke="#23215e" stroke-width="3" d="M18 30l12-10 12 10v12H18z"/><rect x="26" y="32" width="8" height="10" fill="#23215e"/></svg>
      <h3>Selecting a House</h3>
      <p>May not seem like a strong determining factor overall for qualifying for rent to own but it is for us.</p>
      <a class="more">READ MORE</a>
    </div>
  </section>

  <section class="welcome">
    <div class="welcome-bg" role="img" aria-label="Photo of a cream stucco home with terracotta roof under a cloudy blue sky"></div>
    <div class="welcome-panel">
      <h2>WELCOME TO OUR SITE</h2>
      <p>We know life sometimes delivers challenges and it can be hard to get back on track once you have dealt with challenges. Maybe you have been through a divorce, bankruptcy, consumer proposal, loss of job, work place injury, new to the country, self-employed or some credit related challenges that have you behind the eight ball?</p>
      <a class="btn">READ MORE</a>
    </div>
    <div class="types">
      <div class="type" style="left:134px">Fixed<br>Rate Mortgages</div>
      <div class="divider" style="left:293px"></div>
      <div class="type" style="left:340px">Variable<br>Rate Mortgages</div>
      <div class="divider" style="left:503px"></div>
      <div class="type" style="left:552px">Discount<br>Rate Mortgages</div>
      <div class="divider" style="left:712px"></div>
      <div class="type" style="left:758px">Interest only<br>Mortgages</div>
      <div class="divider" style="left:904px"></div>
      <div class="type" style="left:948px">Cashback<br>Rate Mortgages</div>
    </div>
  </section>

  <section class="testimonials">
    <h2 class="sec-title" style="top:1822px">TESTIMONIALS</h2>
    <div class="sec-rule" style="top:1865px"></div>
    <span class="qmark" style="left:355px;top:1876px">&ldquo;</span>
    <p class="quote">There are many variations of passages of Lorem Ipsum available, but the majority have suffered alteration in some form, by injected humour, or randomised words which don't look even slightly believable. If you are going to use a passage of Lorem Ipsum, you need.</p>
    <span class="qmark" style="left:735px;top:1990px">&rdquo;</span>
    <p class="author">DANIEL ORTIZ</p>
    <a class="arrow" style="left:214px"><svg width="10" height="10" viewBox="0 0 10 10"><path d="M6.5 1.5L3 5l3.5 3.5" fill="none" stroke="#444" stroke-width="1.4"/></svg></a>
    <a class="arrow" style="left:926px"><svg width="10" height="10" viewBox="0 0 10 10"><path d="M3.5 1.5L7 5 3.5 8.5" fill="none" stroke="#444" stroke-width="1.4"/></svg></a>
  </section>

  <footer class="footer">
    <div class="f-brand"><span class="mark"></span>Harborline Lending Group</div>

    <h4 class="f-head" style="left:406px">Contact Us</h4>
    <ul class="f-contact">
      <li><svg width="9" height="12" viewBox="0 0 9 12"><path fill="#23215e" d="M4.5 0A4.5 4.5 0 0 0 0 4.5C0 8 4.5 12 4.5 12S9 8 9 4.5A4.5 4.5 0 0 0 4.5 0zm0 6.2a1.7 1.7 0 1 1 0-3.4 1.7 1.7 0 0 1 0 3.4z"/></svg><span>218 Linden Court<br>Ames, IA 50010</span></li>
      <li><svg width="11" height="11" viewBox="0 0 24 24"><path fill="#23215e" d="M6.6 10.8a15.1 15.1 0 0 0 6.6 6.6l2.2-2.2c.3-.3.7-.4 1-.2 1.1.4 2.3.6 3.6.6.6 0 1 .4 1 1V20c0 .6-.4 1-1 1A17 17 0 0 1 3 4c0-.6.4-1 1-1h3.5c.6 0 1 .4 1 1 0 1.3.2 2.5.6 3.6.1.3 0 .7-.2 1z"/></svg><span>555.010.2040</span></li>
      <li><svg width="12" height="9" viewBox="0 0 12 9"><rect width="12" height="9" fill="#23215e"/><path d="M0 0l6 5 6-5" fill="none" stroke="#fff" stroke-width="1"/></svg><span>info@harborlinelending.com</span></li>
    </ul>

    <h4 class="f-head" style="left:679px">Menu</h4>
    <ul class="f-menu"><li>Home</li><li>About</li><li>Types of mortgages</li><li>Rent to own</li><li>Contact us</li></ul>

    <h4 class="f-head" style="left:859px">Newsletter Signup</h4>
    <div class="f-input"><svg width="12" height="9" viewBox="0 0 12 9"><rect width="12" height="9" fill="#23215e"/><path d="M0 0l6 5 6-5" fill="none" stroke="#fff" stroke-width="1"/></svg>E mail id</div>
    <a class="f-btn">SIGNUP</a>

    <div class="f-rule"></div>
    <div class="follow"><span class="lbl">Follow us</span><span class="c"></span><span class="c"></span><span class="c"></span></div>
    <p class="copy">Copyrights @ 2017 All Rights Reserved</p>
  </footer>

</div>
</body>
</html>
```